Tidewell Horizon Magazine need Logo desing and front page for 1 edittion

This is a new magazine that will be circulating in Panama. the magazine will run non for profit,will be mostly informative and few advertizers to cover printing costs.
the magaine will oncce every 2 or 3 month. we need to present it to the editors who will be aproving or diss aproving the project.

we need a Logo desing for the name of the magazine "Tidewell Horizon" and the "front cover desing for the first edition" it will be good if the designer can incude the designed format for the iner magazine, for us just to add in the artucles and the spaces for advertizing.

the magazine content will be articles by govenment energy sectors, gloval warming articles, articles in renewvable enery, university profesor talking or promoting new ideas or university advances, orientations, special edition on book or international articles about the subject on saving enerty, different sectors, world innovations in renewbable energy, and the companies who will advertize will be comapnies selling VORN products, companies offfering product and services on renewvable energy, Led product and systems companies etc...

Printing

```html
<!DOCTYPE html>
<html lang="en">
<head>
<meta charset="utf-8">
<title>Tidewell Horizon — Issue 1 Cover</title>
<link rel="stylesheet" href="https://fonts.googleapis.com/css2?family=Josefin+Sans:wght@300;700&family=Roboto+Condensed:wght@700&display=swap">
<style>
  :root {
    --backdrop: #e6e6e6;
    --paper: #f2f2f2;
    --ink: #111111;
    --leaf: #2f7d33;
    --photo-light: #d9d9d9;
    --photo-mid: #a9a9a9;
    --photo-dark: #7c7c7c;
  }
  html, body {
    margin: 0;
    width: 1200px;
    height: 1000px;
    overflow: hidden;
    background: var(--backdrop);
  }
  .cover {
    position: absolute;
    left: 250px;
    top: 42px;
    width: 702px;
    height: 908px;
    background: var(--paper);
    box-shadow: 3px 4px 8px rgba(0,0,0,0.35);
    overflow: hidden;
  }
  .cover-photo {
    position: absolute;
    left: 0;
    top: 200px;
    width: 100%;
    height: 708px;
    background: linear-gradient(180deg,
      var(--paper) 0%,
      var(--photo-light) 10%,
      var(--photo-mid) 35%,
      #9a9a9a 60%,
      var(--photo-dark) 100%);
  }
  .masthead {
    position: absolute;
    left: 34px;
    top: 30px;
    width: 630px;
    margin: 0;
    font-family: "Josefin Sans", sans-serif;
    font-weight: 300;
    color: var(--ink);
    line-height: 0.85;
    text-transform: lowercase;
  }
  .masthead span { display: block; }
  .masthead .line-one { font-size: 128px; letter-spacing: 2px; }
  .masthead .line-two { font-size: 110px; text-align: right; }
  .headline {
    position: absolute;
    margin: 0;
    font-family: "Josefin Sans", sans-serif;
    font-weight: 700;
    color: var(--leaf);
    text-transform: uppercase;
    letter-spacing: 3px;
    line-height: 1.08;
    text-shadow: 3px 3px 0 var(--ink);
  }
  .deck {
    position: absolute;
    margin: 0;
    font-family: "Roboto Condensed", sans-serif;
    font-weight: 700;
    color: var(--ink);
  }
  .story-power { left: 40px; top: 283px; font-size: 33px; }
  .deck-power { left: 38px; top: 412px; font-size: 17px; line-height: 1.27; }
  .story-envy { left: 40px; top: 527px; font-size: 33px; }
  .deck-envy { left: 38px; top: 610px; font-size: 17px; line-height: 1.27; }
  .story-top { right: 40px; top: 620px; font-size: 54px; text-align: right; line-height: 1.0; }
  .deck-top { right: 40px; top: 808px; font-size: 24px; line-height: 1.25; text-align: right; }
</style>
</head>
<body>
  <main class="cover">
    <div class="cover-photo" role="img" aria-label="Grayscale photograph of an open-cast mining landscape with power pylons on a hazy horizon"></div>

    <h1 class="masthead">
      <span class="line-one">tidewell</span>
      <span class="line-two">horizon</span>
    </h1>

    <h2 class="headline story-power">Power<br>People<br>Profits</h2>
    <p class="deck deck-power">Bank on Community<br>Power to Defeat Wind<br>NIMBY Syndrome</p>

    <h2 class="headline story-envy">USA Green<br>with Envy</h2>
    <p class="deck deck-envy">Dana Whitlock Speaks out<br>about Panama’s green<br>energy plans</p>

    <h2 class="headline story-top">Top 20<br>Movers<br>&amp; Shakers</h2>
    <p class="deck deck-top">Panama’s Rural Renewable<br>Energy Renaissance</p>
  </main>
</body>
</html>
```